Business card

I need a business card design for my consulting company in animal welfare for livestock. I like clean, crisp, simple.

One I imagined was double-sided:
side1: just my name and contact information
side2: silhouette of farm animals. Could be 3 (pig, cow, chicken) or all the species (pig, cow, chicken, duck, sheep, rabbit, etc) that continue the length of the card. I have attached an image of a silhouette style.

But, I am open to any concept.

```html
<!DOCTYPE html>
<html lang="en">
<head>
<meta charset="UTF-8">
<title>Business Card – Humane Practices for Livestock Producers</title>
<link rel="stylesheet" href="https://fonts.googleapis.com/css2?family=Arimo:wght@400&display=swap">
<style>
  :root {
    --card-bg: #ffffff;
    --ink: #000000;
  }
  html, body {
    margin: 0;
    padding: 0;
    width: 1200px;
    height: 741px;
    overflow: hidden;
    background: var(--card-bg);
  }
  .card {
    position: relative;
    width: 1200px;
    height: 741px;
    background: var(--card-bg);
    color: var(--ink);
    font-family: "Arimo", Arial, Helvetica, sans-serif;
    font-weight: 400;
  }
  .card__line {
    position: absolute;
    left: 0;
    width: 100%;
    margin: 0;
    text-align: center;
    font-size: 54px;
    line-height: 1;
    font-weight: 400;
    white-space: nowrap;
  }
  .company-name  { top: 89px; }
  .person-name   { top: 348px; }
  .contact-phone { top: 543px; }
  .contact-email { top: 607px; }
</style>
</head>
<body>
  <main class="card">
    <h1 class="card__line company-name">Humane Practices for Livestock Producers</h1>
    <p class="card__line person-name">Maren Holloway</p>
    <p class="card__line contact-phone">+1.604.555.0172</p>
    <p class="card__line contact-email">maren.holloway@fieldmail.com</p>
  </main>
</body>
</html>
```